Coral Wing Flights brochure

A single A4 brochures that is tri-folded and shows some of our tour packages with contact details.

Please visit www.coralwingflights.com.au to see the designs and images that can be used.

I want to provide designers the freedom to try something creative because I want to give prospective client - normally tourists to Sydney a quality service. I want the brochure to reflect this.

The image on the front page needs to be of the Sydney Harbour. The image MUST be in daylight - not night time.

I have now provided an image of the aircraft (in GIF format). Please use this image and place it over the image of the sydney harbour bridge and quayside concert pavilion.

I may need to discuss this further but what I have not show in the attached files is a small form I will like the client to fill out..

Reservation number
Name
Address
Phone number
Email

We can discuss this at a latter time.

The QR Code needs to contain your web address (www.coralwingflights.com.au)

Target Market(s)

Visitors and tourists to Sydney who want a day trip.
We are providing an exciting way to see Sydney. By air in a light aircraft...

Industry/Entity Type

House

Font styles to use
Sans Serif
Script

Colors
33a6d7
3276b5
85acd3
85cae6
ffffff

Requirements
Must have
• Brochure must be A4 (with about 2 to 3mm bleed - so it can be cut at the printers). They but be folded in 3 to produce a DL size brochure.

The words "Prepare to be amazed" should be in script font...

Please use the following wording for our Terms can conditions...

Terms and Conditions
Coral Wing Flights operates from Merrowdale Airfield within Sydney’s busy airspace Your chosen flight may be subject to delays. Clearance to enter controlled airspace may be refused - this is especially true of our popular Coastline Panorama flight. If this happens, we can either offer other suitable flights, reschedule the flight or, if this isn’t suitable, we provide a refund.
Other aircraft, besides our standard Talbin Skyrunners, are available if we consider they better suit your requirements.
See our web site www.coralwingflights.com.au for full details.
Coral Wing Flights is a trading name of Orvexa Pty Limited
(ABN 81 417 286 309) which operates under the Air Operators Certificate (AOC) of Dorrigan and Welsford Pty Ltd.
Nice to have
• Suggestion - on one of the sides (with the packages) to have a background image.

Suggestion is to keep the brochure light and "airy"

```html
<!DOCTYPE html>
<html lang="en">
<head>
<meta charset="utf-8">
<title>Coral Wing Flights – Tour Packages</title>
<link href="https://fonts.googleapis.com/css2?family=Open+Sans:wght@300;400;700;800&display=swap" rel="stylesheet">
<style>
  :root {
    --brand-blue: #33a6d7;
    --ink: #1f1f1f;
    --paper: #ffffff;
  }
  * { box-sizing: border-box; margin: 0; padding: 0; }
  html, body { width: 1200px; height: 849px; overflow: hidden; background: var(--paper); }
  body { position: relative; font-family: "Open Sans", Arial, sans-serif; color: var(--ink); }

  .package { position: absolute; top: 0; width: 400px; height: 817px; }
  .package--harbour { left: 0; }
  .package--coastal { left: 400px; }
  .package--mountains { left: 800px; }

  .package__tab { position: absolute; top: 0; left: 0; width: 336px; height: 66px; }
  .package__title {
    position: absolute; top: 21px; left: 18px;
    color: var(--paper); font-weight: 400; font-size: 16px; letter-spacing: 0.1px;
  }

  .package__photo { position: absolute; top: 67px; left: 0; width: 400px; height: 269px; }
  .photo--harbour { background: linear-gradient(160deg, #b9c6cc 0%, #6f8a7e 30%, #5b8a97 55%, #3f7389 80%, #8a6b5e 100%); }
  .photo--coastal { background: linear-gradient(180deg, #4f93cf 0%, #b9d5ec 32%, #6f8c6a 45%, #1f4f86 60%, #173f75 100%); }
  .photo--mountains { background: linear-gradient(110deg, #7b5a2a 0%, #c7873b 35%, #d9a25a 50%, #5f7a4a 70%, #3e5a34 100%), linear-gradient(180deg, #8c9fd4, #c9a7c9); }

  .package__price {
    position: absolute; top: 336px; left: 0; width: 400px; text-align: center;
    color: var(--brand-blue); font-weight: 800; white-space: nowrap;
  }
  .price__amount { font-size: 50px; }
  .price__unit { font-size: 33px; font-weight: 700; }

  .package__duration {
    position: absolute; top: 412px; left: 0; width: 400px; text-align: center;
    font-size: 14px;
  }
  .package__duration strong { font-weight: 700; }
  .package__duration svg { vertical-align: -1px; margin-right: 4px; }

  .package__stops { position: absolute; top: 502px; list-style: none; font-size: 21px; line-height: 31.5px; }
  .package--harbour .package__stops { left: 72px; }
  .package--coastal .package__stops { left: 17px; }
  .package--mountains .package__stops { left: 93px; }
  .package__stops li { position: relative; padding-left: 26px; }
  .package__stops li svg { position: absolute; left: 0; top: 8px; }

  .footer-band { position: absolute; left: 0; bottom: 0; width: 1200px; height: 32px; background: var(--brand-blue); }
</style>
</head>
<body>
<svg width="0" height="0" style="position:absolute">
  <defs>
    <symbol id="icon-plane" viewBox="0 0 16 16">
      <rect width="16" height="16" fill="#111"/>
      <path d="M3 12 L12 4 L13 5 L9 9 L11 13 L10 13.5 L7.5 10.5 L5 12.5 L5.5 14 L4.5 14 Z" fill="#fff"/>
    </symbol>
    <symbol id="icon-clock" viewBox="0 0 12 12">
      <circle cx="6" cy="6" r="5" fill="none" stroke="#222" stroke-width="1.2"/>
      <path d="M6 3 V6 L8 7" fill="none" stroke="#222" stroke-width="1.2"/>
    </symbol>
    <symbol id="tab-shape" viewBox="0 0 336 66">
      <polygon points="0,0 280,0 336,66 0,66" fill="#33a6d7"/>
    </symbol>
  </defs>
</svg>

<section class="package package--harbour">
  <svg class="package__tab"><use href="#tab-shape"/></svg>
  <h2 class="package__title">Sydney Harbour Scenic</h2>
  <div class="package__photo photo--harbour" role="img" aria-label="Aerial photo of Sydney Harbour, the city skyline, the harbour bridge and the concert pavilion"></div>
  <p class="package__price"><span class="price__amount">$ 560</span> <span class="price__unit">per aircraft</span></p>
  <p class="package__duration"><svg width="11" height="11"><use href="#icon-clock"/></svg><strong>Duration:</strong> 1 hour 20 mins</p>
  <ul class="package__stops">
    <li><svg width="16" height="16"><use href="#icon-plane"/></svg>Parramatta City</li>
    <li><svg width="16" height="16"><use href="#icon-plane"/></svg>Hornsby</li>
    <li><svg width="16" height="16"><use href="#icon-plane"/></svg>Bahai Temple</li>
    <li><svg width="16" height="16"><use href="#icon-plane"/></svg>Sydney Harbour Bridge</li>
    <li><svg width="16" height="16"><use href="#icon-plane"/></svg>Quayside Concert Pavilion</li>
    <li><svg width="16" height="16"><use href="#icon-plane"/></svg>Manly</li>
    <li><svg width="16" height="16"><use href="#icon-plane"/></svg>Long Reef</li>
  </ul>
</section>

<section class="package package--coastal">
  <svg class="package__tab"><use href="#tab-shape"/></svg>
  <h2 class="package__title">Sydney Coastal</h2>
  <div class="package__photo photo--coastal" role="img" aria-label="Aerial photo of Sydney's coastal cliffs and deep blue ocean under a clear sky"></div>
  <p class="package__price"><span class="price__amount">$ 560</span> <span class="price__unit">per aircraft</span></p>
  <p class="package__duration"><svg width="11" height="11"><use href="#icon-clock"/></svg><strong>Duration:</strong> 1 hour 20 mins</p>
  <ul class="package__stops">
    <li><svg width="16" height="16"><use href="#icon-plane"/></svg>Cambelltown</li>
    <li><svg width="16" height="16"><use href="#icon-plane"/></svg>Stanwell Park</li>
    <li><svg width="16" height="16"><use href="#icon-plane"/></svg>Entrance of Port Hacking</li>
    <li><svg width="16" height="16"><use href="#icon-plane"/></svg>Entrance of Botany Bay</li>
    <li><svg width="16" height="16"><use href="#icon-plane"/></svg>Famous Sydney Beaches including<br>Maroubra, Cooge, Bondi &amp; Manly</li>
    <li><svg width="16" height="16"><use href="#icon-plane"/></svg>Sydney Heads</li>
    <li><svg width="16" height="16"><use href="#icon-plane"/></svg>Long Reef</li>
  </ul>
</section>

<section class="package package--mountains">
  <svg class="package__tab"><use href="#tab-shape"/></svg>
  <h2 class="package__title">The Blue Mountains</h2>
  <div class="package__photo photo--mountains" role="img" aria-label="Photo of sunlit sandstone rock pillars above a forested Blue Mountains valley"></div>
  <p class="package__price"><span class="price__amount">$ 475</span> <span class="price__unit">per aircraft</span></p>
  <p class="package__duration"><svg width="11" height="11"><use href="#icon-clock"/></svg><strong>Duration:</strong> 1 hour 10 mins</p>
  <ul class="package__stops">
    <li><svg width="16" height="16"><use href="#icon-plane"/></svg>Katoomba</li>
    <li><svg width="16" height="16"><use href="#icon-plane"/></svg>The Three Sisters</li>
    <li><svg width="16" height="16"><use href="#icon-plane"/></svg>Warragamba Dam</li>
    <li><svg width="16" height="16"><use href="#icon-plane"/></svg>Prospect Resrvour</li>
  </ul>
</section>

<div class="footer-band"></div>
</body>
</html>
```